Website Design for Landscaping/Concrete Company

I need a website that is informative about what my company does and also offers before and after pictures of completed work. I already have a logo. The website must say "FREE ESTIMATES" somewhere and list a phone number. I would like to stick with the logo colors or similar (black and lime green).
Services Offered by Tomlet Builders:
Landscaping
Mowing
Concrete
Sidewalks
Brush Removal
Land Beautification

Please list the company name in large letters TOMLET BUILDERS
and also the contact information in large font.

Right now I am looking for a somewhat coverpage for my website. I don't have a lot of information for people to point and click on yet. Id like to get a coverpage to get my name out and then have a designer come back in a few months and update with more pictures and information.
Updates

If allowed please submit projects after due date. I made a mistake and only posted for one day. Thanks.

Coding

Coded - Design and coding required

```html
<!DOCTYPE html>
<html lang="en">
<head>
<meta charset="utf-8">
<title>Tomlet Builders</title>
<link href="https://fonts.googleapis.com/css2?family=Poppins:wght@400;500;600;700&family=Roboto:wght@300;500&display=swap" rel="stylesheet">
<style>
:root{
  --lime:#8db31b;
  --lime-bright:#b9d822;
  --lime-soft:#f0f3de;
  --icon-line:#7fa51a;
  --ink:#222;
  --muted:#6b6b6b;
  --header:#0d0d0d;
  --works-bg:#f8f7f2;
  --footer:#262626;
  --footer-bottom:#1c1c1c;
  --rule:#e3e3e3;
}
*{box-sizing:border-box;margin:0;padding:0}
html,body{width:1200px;height:3486px;overflow:hidden}
body{position:relative;font-family:'Poppins',sans-serif;color:var(--ink);background:#fff}
.abs{position:absolute}
a{color:inherit;text-decoration:none}

/* header */
.site-header{left:0;top:0;width:1200px;height:85px;background:var(--header)}
.brand{left:234px;top:26px;display:flex;align-items:center;gap:6px;color:var(--lime-bright);font-weight:600;font-size:13px;letter-spacing:.5px;line-height:1.1}
.brand .mark{width:10px;height:10px;background:var(--lime-bright)}
.nav{top:51px;left:497px;display:flex;font-size:10.5px;font-weight:500;color:#fff}
.nav a{position:absolute;white-space:nowrap}
.phone{left:850px;top:13px;color:#fff;font-size:13.5px;font-weight:500;display:flex;align-items:center;gap:8px}
.btn-estimate{left:846px;top:44px;width:120px;height:26px;background:var(--lime);color:#fff;font-size:9px;font-weight:600;display:flex;align-items:center;justify-content:center;border-radius:2px}

/* hero */
.hero{left:0;top:85px;width:1200px;height:459px;background:linear-gradient(135deg,#4a3a2c 0%,#6b5a44 35%,#8a7f6a 60%,#3d372e 100%)}
.hero-shade{left:0;top:85px;width:1200px;height:459px;background:rgba(0,0,0,.28)}
.hero-title{left:0;top:240px;width:1200px;text-align:center;font-family:'Roboto',sans-serif}
.hero-title .pre{display:block;color:#fff;font-weight:300;font-size:32px}
.hero-title .name{display:block;color:var(--lime-bright);font-weight:500;font-size:40px;margin-top:2px}

/* section heads */
.sec-label{font-size:14.5px;font-weight:500;color:var(--lime)}
.sec-tag{font-size:14.5px;font-weight:500;color:#444;text-align:right}
.sec-rule{height:1px;background:var(--rule)}

.about-text{left:234px;top:650px;width:310px;font-size:9.6px;line-height:15px;color:var(--muted)}
.about-text p{margin-bottom:14px}
.photo{background:linear-gradient(135deg,#5d9a2c,#8cc04a 55%,#d2651d)}

/* strip */
.strip{left:0;top:952px;width:1200px;height:171px;display:flex;overflow:hidden}
.strip div{flex:0 0 188px;height:171px}

/* services */
.service{position:absolute;width:215px}
.service .icon{width:76px;height:76px;border-radius:50%;background:var(--lime-soft);display:flex;align-items:center;justify-content:center}
.service .icon svg{width:42px;height:42px;fill:none;stroke:var(--icon-line);stroke-width:1.6;stroke-linecap:round;stroke-linejoin:round}
.service h3{font-size:14.5px;font-weight:600;margin-top:14px;color:#222}
.service p{font-size:9.6px;line-height:15px;color:var(--muted);margin-top:5px}
.service .more{display:inline-block;margin-top:10px;font-size:7px;font-weight:600;color:var(--lime);border-bottom:1px solid var(--lime)}

/* works */
.works{left:0;top:1782px;width:1200px;height:552px;background:var(--works-bg)}
.works-title{left:0;top:1822px;width:1200px;text-align:center;font-size:20px;font-weight:600;color:#222}
.works-title span{color:var(--lime)}
.tabs{top:1870px;font-size:7.5px;font-weight:600;color:#333}
.tabs span{position:absolute;white-space:nowrap}
.tabs .active{color:var(--lime);border-bottom:1px solid var(--lime);padding:0 6px 4px}
.tile{position:absolute;width:188px;height:170px}

/* estimation */
.estimate{left:0;top:2334px;width:1200px;height:425px;background:radial-gradient(ellipse at 75% 40%,#3c3a33 0%,#1d1f1a 55%,#141812 100%)}
.estimate-title{left:0;top:2370px;width:1217px;text-align:center;color:#fff;font-size:20px;font-weight:600}
.field{position:absolute;border:1px solid var(--lime);background:rgba(70,90,10,.35);color:#fff;font-size:8.5px;font-weight:600;padding:0 12px;display:flex;align-items:center}
.field.area{align-items:flex-start;padding-top:14px}
.btn-submit{left:544px;top:2684px;width:149px;height:33px;background:var(--lime);color:#fff;font-size:8px;font-weight:600;display:flex;align-items:center;justify-content:center}

/* map */
.map{left:0;top:2759px;width:1200px;height:362px;background:
  radial-gradient(ellipse 260px 140px at 820px 110px,#8fcf98 0%,rgba(143,207,152,0) 100%),
  radial-gradient(ellipse 300px 120px at 830px 270px,#93d19b 0%,rgba(147,209,155,0) 100%),
  radial-gradient(ellipse 200px 110px at 580px 200px,#a9dbad 0%,rgba(169,219,173,0) 100%),
  radial-gradient(ellipse 240px 120px at 330px 120px,#d9ead0 0%,rgba(217,234,208,0) 100%),
  radial-gradient(ellipse 220px 130px at 260px 300px,#cfe4c6 0%,rgba(207,228,198,0) 100%),
  radial-gradient(ellipse 180px 100px at 1080px 200px,#b3dcb4 0%,rgba(179,220,180,0) 100%),
  linear-gradient(120deg,#c2e2c3,#b2dab5 40%,#a6d5aa 70%,#c4e3c2)}
.map-pin{left:468px;top:2891px;width:69px;height:64px;background:#1a1a1a;display:flex;align-items:center;justify-content:center;text-align:center;color:var(--lime-bright);font-size:9px;font-weight:600;line-height:1.2}
.map-pin-tip{left:495px;top:2955px;width:0;height:0;border-left:8px solid transparent;border-right:8px solid transparent;border-top:9px solid #1a1a1a}

/* footer */
.site-footer{left:0;top:3121px;width:1200px;height:305px;background:var(--footer)}
.foot-brand{left:243px;top:3208px;color:var(--lime-bright);font-size:12px;font-weight:600;display:flex;align-items:center;gap:6px}
.foot-brand .mark{width:9px;height:9px;background:var(--lime-bright)}
.foot-info{left:242px;top:3242px;color:#fff;font-size:10px;font-weight:600;line-height:19px}
.foot-mail{left:239px;top:3335px;color:var(--lime-bright);font-size:10px;line-height:19px}
.foot-col h4{font-size:14.5px;font-weight:600;color:#fff}
.foot-col ul{list-style:none;margin-top:22px;color:#ddd;font-size:10px}
.quick li{height:25px}
.svc li{height:25px}
.social{left:890px;top:3277px;display:flex;gap:14px}
.social span{width:11px;height:11px;border-radius:50%;background:#8a8a8a}
.social span:first-child{background:var(--lime)}
.foot-bottom{left:0;top:3426px;width:1200px;height:60px;background:var(--footer-bottom);color:#aaa;font-size:8.5px;display:flex;align-items:center;justify-content:center}
</style>
</head>
<body>

<header class="abs site-header"></header>
<div class="abs brand"><span class="mark"></span>TOMLET<br>BUILDERS</div>
<nav class="abs nav">
  <a style="left:0">HOME</a>
  <a style="left:65px">ABOUT</a>
  <a style="left:133px">SERVICES</a>
  <a style="left:213px">GALLERY</a>
  <a style="left:276px">CONTACT</a>
</nav>
<div class="abs phone">
  <svg width="12" height="12" viewBox="0 0 24 24"><path fill="#8db31b" d="M6.6 10.8a15.1 15.1 0 0 0 6.6 6.6l2.2-2.2c.3-.3.7-.4 1-.2 1.1.4 2.3.6 3.6.6.6 0 1 .4 1 1V20c0 .6-.4 1-1 1A17 17 0 0 1 3 4c0-.6.4-1 1-1h3.5c.6 0 1 .4 1 1 0 1.3.2 2.5.6 3.6.1.3 0 .7-.2 1z"/></svg>
  1800 -555- 0199
</div>
<a class="abs btn-estimate">FREE ESTIMATION</a>

<section>
  <div class="abs hero" role="img" aria-label="Worker laying paving bricks with a rubber mallet"></div>
  <div class="abs hero-shade"></div>
  <h1 class="abs hero-title"><span class="pre">WELCOME TO</span><span class="name">TOMLET BUILDERS</span></h1>
</section>

<section>
  <div class="abs sec-label" style="left:234px;top:582px">ABOUT US</div>
  <div class="abs sec-tag" style="left:765px;top:568px;width:200px">WHO WE ARE</div>
  <div class="abs sec-rule" style="left:346px;top:597px;width:619px"></div>
  <div class="abs about-text">
    <p>Lorem ipsum dolor sit amet, consectetur adipiscing elit, sed do eiusmod tempor incididunt ut labore et dolore magna aliqua. Quis ipsum suspendisse ultrices gravida. Risus commodo viverra maecenas accumsan lacus vel facilisis.</p>
    <p>Lorem ipsum dolor sit amet, consectetur adipiscing elit, sed do eiusmod tempor incididunt ut labore et dolore magna aliqua. Quis ipsum suspendisse ultrices gravida. Risus commodo viverra maecenas accumsan lacus vel facilisis.</p>
    <p>Lorem ipsum dolor sit amet, consectetur adipiscing elit, sed do eiusmod tempor incididunt ut labore et dolore magna aliqua. Quis ipsum suspendisse ultrices gravida. Risus commodo viverra maecenas accumsan lacus vel facilisis.</p>
  </div>
  <div class="abs photo" style="left:606px;top:641px;width:359px;height:261px" role="img" aria-label="Gloved hand pushing an orange lawn mower on grass"></div>
</section>

<div class="abs strip">
  <div role="img" aria-label="Garden path through flower beds" style="background:linear-gradient(135deg,#3f7a2a,#9bb95a 60%,#e3a448)"></div>
  <div role="img" aria-label="Lawn mower on striped grass" style="background:linear-gradient(135deg,#5a9a34,#2f5a22 60%,#6aa83c)"></div>
  <div role="img" aria-label="Workers finishing fresh concrete" style="background:linear-gradient(135deg,#a5845e,#c9a37a 50%,#5b4736)"></div>
  <div role="img" aria-label="Curved sidewalk beside a lawn" style="background:linear-gradient(135deg,#9ec5e6,#b9b9b2 45%,#5f9a3a)"></div>
  <div role="img" aria-label="Gardener trimming hedges" style="background:linear-gradient(135deg,#3d6f2c,#7a9e5a 55%,#4c7c30)"></div>
  <div role="img" aria-label="Gardener planting flowers" style="background:linear-gradient(135deg,#e08a2a,#6aa63a 50%,#c0392b)"></div>
  <div role="img" aria-label="Mower on sunny grass" style="background:linear-gradient(135deg,#c7b86a,#8fb33f 60%,#4e7a2a)"></div>
</div>

<section>
  <div class="abs sec-label" style="left:234px;top:1180px">SERVICES</div>
  <div class="abs sec-tag" style="left:765px;top:1168px;width:200px">WHAT WE OFFER</div>
  <div class="abs sec-rule" style="left:346px;top:1192px;width:619px"></div>

  <div class="service" style="left:232px;top:1238px">
    <div class="icon"><svg viewBox="0 0 40 40" aria-hidden="true"><path d="M12 6l-6 9h3l-4 7h14l-4-7h3z"/><path d="M12 22v6"/><path d="M20 20l8-6 8 6v8H20z"/><path d="M26 28v-5h4v5"/><path d="M4 32h32"/><path d="M8 35h24"/></svg></div>
    <h3>Landscaping</h3><p>Lorem ipsum dolor sit amet, consectetur adipiscing elit, sed do eiusmod tempor incididunt ut labore et dolore magna aliqua. Quis ipsum suspendisse ultrices gravida. Risus commodo viverra maecenas</p><a class="more">READMORE</a></div>
  <div class="service" style="left:502px;top:1238px">
    <div class="icon"><svg viewBox="0 0 40 40" aria-hidden="true"><path d="M10 5l9 19"/><path d="M7 6l6-2"/><path d="M14 24h18v6H14z"/><circle cx="17" cy="32" r="3"/><circle cx="29" cy="32" r="3"/></svg></div>
    <h3>Mowing</h3><p>Lorem ipsum dolor sit amet, consectetur adipiscing elit, sed do eiusmod tempor incididunt ut labore et dolore magna aliqua. Quis ipsum suspendisse ultrices gravida. Risus commodo viverra maecenas ac-</p><a class="more">READMORE</a></div>
  <div class="service" style="left:758px;top:1236px">
    <div class="icon"><svg viewBox="0 0 40 40" aria-hidden="true"><path d="M4 28V18h8v10"/><path d="M12 28h24"/><ellipse cx="23" cy="18" rx="11" ry="7"/><path d="M17 14l6 8M22 12l6 9"/><circle cx="9" cy="30" r="3"/><circle cx="22" cy="30" r="3"/><circle cx="31" cy="30" r="3"/></svg></div>
    <h3>Concrete</h3><p>Lorem ipsum dolor sit amet, consectetur adipiscing elit, sed do eiusmod tempor incididunt ut labore et dolore magna aliqua. Quis ipsum suspendisse ultrices gravida. Risus commodo viverra maecenas ac-</p><a class="more">READMORE</a></div>

  <div class="service" style="left:234px;top:1484px">
    <div class="icon"><svg viewBox="0 0 40 40" aria-hidden="true"><path d="M12 5l-6 12h3l-4 8h14l-4-8h3z"/><path d="M12 25v5"/><path d="M28 5l-6 12h3l-4 8h14l-4-8h3z"/><path d="M28 25v5"/><path d="M3 30h34"/><path d="M3 35h34"/></svg></div>
    <h3>Sidewalks</h3><p>Lorem ipsum dolor sit amet, consectetur adipiscing elit, sed do eiusmod tempor incididunt ut labore et dolore magna aliqua. Quis ipsum suspendisse ultrices gravida. Risus commodo viverra maecenas</p><a class="more">READMORE</a></div>
  <div class="service" style="left:506px;top:1484px">
    <div class="icon"><svg viewBox="0 0 40 40" aria-hidden="true"><path d="M22 6l12 12-8 8-12-12z"/><path d="M25 9l6 6M28 6l6 6"/><path d="M14 14l-8 8 4 4 8-8"/><path d="M8 24l-4 10 10-4"/></svg></div>
    <h3>Brush Removal</h3><p>Lorem ipsum dolor sit amet, consectetur adipiscing elit, sed do eiusmod tempor incididunt ut labore et dolore magna aliqua. Quis ipsum suspendisse ultrices gravida. Risus commodo viverra maecenas ac-</p><a class="more">READMORE</a></div>
  <div class="service" style="left:760px;top:1484px">
    <div class="icon"><svg viewBox="0 0 40 40" aria-hidden="true"><path d="M20 30V10"/><circle cx="20" cy="7" r="3"/><path d="M20 18c-4 0-6-3-6-6 4 0 6 3 6 6zM20 22c4 0 6-3 6-6-4 0-6 3-6 6z"/><path d="M10 30V18"/><circle cx="10" cy="15" r="3"/><path d="M30 30V18"/><circle cx="30" cy="15" r="3"/><path d="M5 34c3-4 27-4 30 0z"/></svg></div>
    <h3>Land Beautification</h3><p>Lorem ipsum dolor sit amet, consectetur adipiscing elit, sed do eiusmod tempor incididunt ut labore et dolore magna aliqua. Quis ipsum suspendisse ultrices gravida. Risus commodo viverra maecenas ac-</p><a class="more">READMORE</a></div>
</section>

<section>
  <div class="abs works"></div>
  <h2 class="abs works-title">Our <span>Works</span></h2>
  <div class="abs tabs" style="left:0;width:1200px">
    <span class="active" style="left:347px">ALL</span>
    <span style="left:397px">LANDSCAPING</span>
    <span style="left:487px">MOWING</span>
    <span style="left:555px">CONCRETE</span>
    <span style="left:622px">SIDEWALKS</span>
    <span style="left:690px">BRUSH REMOVAL</span>
    <span style="left:780px">LAND BEAUTIFICATION</span>
  </div>
  <div class="tile" style="left:200px;top:1919px;background:linear-gradient(135deg,#3f7a2a,#9bb95a 60%,#e3a448)" role="img" aria-label="Garden path through flower beds"></div>
  <div class="tile" style="left:403px;top:1919px;background:linear-gradient(135deg,#5a9a34,#2f5a22 60%,#6aa83c)" role="img" aria-label="Lawn mower on striped grass"></div>
  <div class="tile" style="left:607px;top:1919px;background:linear-gradient(135deg,#a5845e,#c9a37a 50%,#5b4736)" role="img" aria-label="Workers finishing fresh concrete"></div>
  <div class="tile" style="left:810px;top:1919px;background:linear-gradient(135deg,#9ec5e6,#b9b9b2 45%,#5f9a3a)" role="img" aria-label="Curved sidewalk beside a lawn"></div>
  <div class="tile" style="left:199px;top:2104px;background:linear-gradient(135deg,#3d6f2c,#7a9e5a 55%,#4c7c30)" role="img" aria-label="Gardener trimming hedges"></div>
  <div class="tile" style="left:402px;top:2104px;background:linear-gradient(135deg,#e08a2a,#6aa63a 50%,#c0392b)" role="img" aria-label="Gardener planting flowers"></div>
  <div class="tile" style="left:606px;top:2104px;background:linear-gradient(135deg,#c7b86a,#8fb33f 60%,#4e7a2a)" role="img" aria-label="Mower on sunny grass"></div>
  <div class="tile" style="left:809px;top:2104px;background:linear-gradient(135deg,#d8c7a8,#c75a5a 40%,#4a7ab0 70%,#7a5a3a)" role="img" aria-label="Colourful painted walkway with a bench"></div>
</section>

<section>
  <div class="abs estimate" role="img" aria-label="Lawn mower on grass, darkened background"></div>
  <h2 class="abs estimate-title">Free Estimation</h2>
  <div class="field" style="left:409px;top:2429px;width:198px;height:38px">First Name</div>
  <div class="field" style="left:622px;top:2429px;width:199px;height:38px">Last Name</div>
  <div class="field" style="left:409px;top:2484px;width:412px;height:37px">Email Address</div>
  <div class="field" style="left:409px;top:2536px;width:412px;height:36px">Phone Number</div>
  <div class="field area" style="left:409px;top:2590px;width:412px;height:69px">Message</div>
  <a class="abs btn-submit">GET ESTIMATION</a>
</section>

<section>
  <div class="abs map" role="img" aria-label="Road map of the service area with forests and towns"></div>
  <div class="abs map-pin">TOMLET<br>BUILDERS</div>
  <div class="abs map-pin-tip"></div>
</section>

<footer>
  <div class="abs site-footer"></div>
  <div class="abs foot-brand"><span class="mark"></span>TOMLET BUILDERS</div>
  <div class="abs foot-info">Address line 1<br>Address line 2<br>Location<br>Mobile Number</div>
  <div class="abs foot-mail">Email address line 1<br>Email address line 2</div>
  <div class="abs foot-col quick" style="left:522px;top:3176px">
    <h4>Quick Links</h4>
    <ul><li>Home</li><li>About us</li><li>Services</li><li>Blog</li><li>Contact us</li></ul>
  </div>
  <div class="abs foot-col svc" style="left:691px;top:3176px">
    <h4>Our Services</h4>
    <ul><li>Landscaping</li><li>Mowing</li><li>Concrete</li><li>Sidewalks</li><li>Brush Removal</li><li>Land Beautification</li></ul>
  </div>
  <div class="abs social"><span></span><span></span><span></span><span></span></div>
  <div class="abs foot-bottom">Copyright © 2021 TOMLET - All Rights Reserved.</div>
</footer>

</body>
</html>
```